Seeking funky, innovative business cards

I am looking to refresh our current business cards to something more engaging, visual and impactful. We are a management consultancy firm, see website (www.larkstone-partners.com.au). I've included our colour scheme, sample of the slides we use and our old business cards. We would like our cards to have icons. The card should display:- Name- Title- Mobile number- Address- Email address- Website - Company logo- Our purpose statement "We build workplaces people are proud to join"

Contact Information for Business Card

Brennan Ulfsson
Consultant
0468 927 341
Level 3, 218 Wexley Street, Melbourne 3000
brennan@larkstone-partners.com.au
www.larkstone-partners.com.au

Purpose statement "We build workplaces people are proud to join"
LOGO available in google images

Font styles to use
Other font styles liked:
• Open Sans Light, Bebas Neue (open to other cool foints)

Colors
ffc214
5c5c5c
f5f5f5
fefefe

Requirements
Must have
• - Name
• - Title
• - Mobile number
• - Address
• - Email address
• - Website
• - Company logo
• - Our purpose statement "We build workplaces people are proud to join"
Nice to have
• - Icons
• - Colour (see our colour scheme"

```html
<!DOCTYPE html>
<html lang="en">
<head>
<meta charset="utf-8">
<title>Larkstone Partners – Business Card</title>
<link rel="stylesheet" href="https://fonts.googleapis.com/css2?family=Lato:wght@300;400&family=Roboto+Condensed:wght@700&display=swap">
<style>
  :root {
    --backdrop: #8c8c8c;
    --charcoal: #434748;
    --yellow-top: #ffd300;
    --yellow-bottom: #fdbe24;
    --accent: #f7b21d;
    --tagline: #f5a623;
    --paper: #fefefe;
    --ink: #3f4244;
    --light-text: #f5f5f5;
  }
  * { box-sizing: border-box; margin: 0; padding: 0; }
  html, body {
    width: 1200px;
    height: 802px;
    overflow: hidden;
    background: var(--backdrop);
  }
  .canvas { position: relative; width: 1200px; height: 802px; }
  .card {
    position: absolute;
    top: 274px;
    width: 442px;
    height: 265px;
    overflow: hidden;
  }
  .card--front { left: 136px; background: var(--charcoal); }
  .card--back { left: 624px; background: var(--paper); }

  .front-accent { position: absolute; inset: 0; }

  .contact {
    position: absolute;
    left: 19px;
    top: 63px;
    font-family: 'Lato', sans-serif;
    color: var(--light-text);
  }
  .contact__name {
    font-size: 17px;
    font-weight: 400;
    color: var(--accent);
    letter-spacing: 0.1px;
    line-height: 19px;
  }
  .contact__title { font-size: 13px; line-height: 16px; }
  .contact__address { margin-top: 13px; font-size: 13px; line-height: 16px; }
  .contact__list { list-style: none; margin-top: 13px; font-size: 13px; line-height: 16px; }
  .contact__list li { display: flex; align-items: center; gap: 4px; }
  .contact__icon { width: 10px; height: 10px; flex: none; }

  .brand {
    position: absolute;
    left: 0; right: 0;
    top: 94px;
    display: flex;
    justify-content: center;
    align-items: center;
    gap: 10px;
  }
  .brand__dot {
    width: 10px; height: 10px;
    border-radius: 50%;
    background: var(--yellow-bottom);
  }
  .brand__name {
    font-family: 'Lato', sans-serif;
    font-weight: 300;
    font-size: 36px;
    color: var(--ink);
  }
  .purpose {
    position: absolute;
    left: 0; right: 0; bottom: 0;
    height: 46px;
    background: var(--charcoal);
    display: flex;
    align-items: center;
    justify-content: center;
    font-family: 'Roboto Condensed', sans-serif;
    font-weight: 700;
    font-size: 13px;
    color: var(--tagline);
    text-transform: uppercase;
    white-space: nowrap;
  }
</style>
</head>
<body>
<main class="canvas">
  <section class="card card--front">
    <svg class="front-accent" width="442" height="265" viewBox="0 0 442 265" aria-hidden="true">
      <defs>
        <linearGradient id="accentFill" x1="0" y1="0" x2="0" y2="1">
          <stop offset="0" stop-color="#ffd300"/>
          <stop offset="1" stop-color="#fdbe24"/>
        </linearGradient>
      </defs>
      <polygon points="292,0 442,0 442,265 224,265 391,138" fill="url(#accentFill)"/>
    </svg>
    <div class="contact">
      <h1 class="contact__name">BRENNAN ULFSSON</h1>
      <p class="contact__title">Consultant</p>
      <p class="contact__address">Level 3, 218 Wexley<br>Street, Melbourne 3000</p>
      <ul class="contact__list">
        <li>
          <svg class="contact__icon" viewBox="0 0 10 10" aria-label="Phone"><path d="M0.5 4 Q5 0.5 9.5 4 L8.3 5.3 L6.6 4.3 L6.6 3.4 Q5 2.9 3.4 3.4 L3.4 4.3 L1.7 5.3 Z" fill="var(--accent)"/><rect x="2.2" y="5.4" width="5.6" height="3.6" rx="0.6" fill="var(--accent)"/></svg>
          0468 927 341
        </li>
        <li>
          <svg class="contact__icon" viewBox="0 0 10 10" aria-label="Email"><rect x="0.5" y="2" width="9" height="6.5" fill="var(--accent)"/><path d="M0.8 2.3 L5 5.8 L9.2 2.3" stroke="var(--charcoal)" stroke-width="0.9" fill="none"/></svg>
          brennan@larkstone-partners.com.au
        </li>
        <li>
          <svg class="contact__icon" viewBox="0 0 10 10" aria-label="Website"><circle cx="5" cy="5" r="4.5" fill="var(--accent)"/><path d="M0.8 5 H9.2 M5 0.6 Q2.5 5 5 9.4 M5 0.6 Q7.5 5 5 9.4" stroke="var(--charcoal)" stroke-width="0.7" fill="none"/></svg>
          www.larkstone-partners.com.au
        </li>
      </ul>
    </div>
  </section>

  <section class="card card--back">
    <div class="brand">
      <span class="brand__dot"></span>
      <span class="brand__name">Larkstone Partners</span>
    </div>
    <p class="purpose">We build workplaces people are proud to join</p>
  </section>
</main>
</body>
</html>
```